Hedge trimming service requires large business signage for side of trailer

Create a signage design for my business, Fernleaf Verge Clipping, a hedge trimming service, which will be used for advertising on a trailer. Design for signage will be created from existing photo supplied.
Dimensions of proposed sign: 600x1200cm
My website: https://www.fernleafvergeclipping.com.au/
Colours we like: green, black, sky blue, white & orange (Kravo logo)
Words to be used with graphic design:
Fernleaf Verge Clipping
Southern Highlands
P Mabel 0417 251 964
W fernleafvergeclipping.com.au
Have your hedges trimmed today!

Fernleaf Verge Clipping/Southern Highlands/Call Mabel 0417 251 964/fernleafvergeclipping.com.au

```html
<!DOCTYPE html>
<html lang="en">
<head>
<meta charset="UTF-8">
<title>Fernleaf Verge Clipping – Trailer Sign</title>
<link href="https://fonts.googleapis.com/css2?family=Poppins:ital,wght@1,300&family=Open+Sans:wght@400;600;700&family=Dancing+Script:wght@700&family=Arimo:wght@700&display=swap" rel="stylesheet">
<style>
  :root {
    --black: #0c0c0c;
    --white: #ffffff;
    --orange: #f04e0c;
    --green: #5cd11e;
    --leaf-dark: #1f3a14;
    --leaf: #4f8a2c;
    --sky: #dfe6ea;
  }
  * { margin: 0; padding: 0; box-sizing: border-box; }
  html, body { width: 1200px; height: 600px; overflow: hidden; background: var(--black); }
  .sign {
    position: relative;
    width: 1200px;
    height: 600px;
    background: var(--black);
    overflow: hidden;
  }
  .sign__art { position: absolute; inset: 0; }
  .business-name {
    position: absolute;
    left: 600px;
    top: 34px;
    width: 600px;
    text-align: center;
    font-family: "Poppins", sans-serif;
    font-style: italic;
    font-weight: 300;
    font-size: 62px;
    line-height: 76px;
    color: var(--white);
    letter-spacing: 0.5px;
  }
  .region {
    position: absolute;
    left: 600px;
    top: 224px;
    width: 600px;
    text-align: center;
    font-family: "Open Sans", sans-serif;
    font-weight: 600;
    font-size: 34px;
    color: var(--orange);
  }
  .contact-name {
    position: absolute;
    left: 600px;
    top: 368px;
    width: 600px;
    text-align: center;
    font-family: "Open Sans", sans-serif;
    font-weight: 600;
    font-size: 39px;
    color: var(--green);
  }
  .phone {
    position: absolute;
    left: 626px;
    top: 432px;
    display: flex;
    align-items: center;
    gap: 16px;
  }
  .phone__icon { width: 60px; height: 60px; }
  .phone__number {
    font-family: "Open Sans", sans-serif;
    font-weight: 700;
    font-size: 72px;
    line-height: 1;
    color: var(--white);
    letter-spacing: 1px;
  }
  .web {
    position: absolute;
    left: 592px;
    top: 544px;
    display: flex;
    align-items: center;
    gap: 14px;
  }
  .web__icon { width: 40px; height: 40px; }
  .web__url {
    font-family: "Arimo", sans-serif;
    font-weight: 700;
    font-size: 31px;
    color: var(--black);
  }
  .tagline {
    position: absolute;
    left: 28px;
    top: 474px;
    font-family: "Open Sans", sans-serif;
    font-weight: 600;
    font-size: 45px;
    line-height: 52px;
    color: var(--white);
    text-transform: uppercase;
  }
  .tagline__accent {
    font-family: "Dancing Script", cursive;
    font-weight: 700;
    text-transform: none;
    font-size: 62px;
    color: var(--green);
  }
</style>
</head>
<body>
<div class="sign">
  <svg class="sign__art" viewBox="0 0 1200 600" width="1200" height="600">
    <defs>
      <linearGradient id="photoTone" x1="0" y1="0" x2="1" y2="0.4">
        <stop offset="0" stop-color="var(--sky)"/>
        <stop offset="0.3" stop-color="#8fae7a"/>
        <stop offset="0.6" stop-color="var(--leaf)"/>
        <stop offset="1" stop-color="var(--leaf-dark)"/>
      </linearGradient>
      <linearGradient id="photoFade" x1="0" y1="0" x2="0" y2="1">
        <stop offset="0.45" stop-color="#000" stop-opacity="0"/>
        <stop offset="0.95" stop-color="#000" stop-opacity="0.92"/>
      </linearGradient>
    </defs>
    <g role="img" aria-label="Photo of a gardener trimming a tall green hedge with long-handled loppers">
      <path d="M0 0 H505 C690 150 690 450 508 600 H0 Z" fill="url(#photoTone)"/>
      <path d="M0 0 H505 C690 150 690 450 508 600 H0 Z" fill="url(#photoFade)"/>
    </g>
    <path class="divider-curve" d="M505 0 C690 150 690 450 508 600" fill="none" stroke="var(--white)" stroke-width="11"/>
    <path class="web-band" d="M585 529 H1200 V600 H538 Z" fill="var(--orange)"/>
  </svg>

  <h1 class="business-name">Fernleaf Verge<br>Clipping</h1>
  <p class="region">Southern Highlands</p>
  <p class="contact-name">Mabel Hartley</p>

  <div class="phone">
    <svg class="phone__icon" viewBox="0 0 60 60" aria-hidden="true">
      <path d="M14 6 C10 7 5 11 5 17 C6 32 26 54 43 55 C49 55 53 50 54 46 L45 38 C43 36 40 37 38 39 L35 42 C28 38 22 32 18 25 L21 22 C23 20 24 17 22 15 Z" fill="var(--green)"/>
      <path d="M33 17 A11 11 0 0 1 43 27" fill="none" stroke="var(--green)" stroke-width="4.5" stroke-linecap="round"/>
      <path d="M34 6 A21 21 0 0 1 54 26" fill="none" stroke="var(--green)" stroke-width="4.5" stroke-linecap="round"/>
    </svg>
    <span class="phone__number">0417 251 964</span>
  </div>

  <div class="web">
    <svg class="web__icon" viewBox="0 0 40 40" aria-hidden="true">
      <g fill="none" stroke="var(--black)" stroke-width="2.6">
        <circle cx="20" cy="20" r="17"/>
        <ellipse cx="20" cy="20" rx="7.5" ry="17"/>
        <line x1="3" y1="20" x2="37" y2="20"/>
        <line x1="20" y1="3" x2="20" y2="37"/>
        <path d="M6 11 H34 M6 29 H34"/>
      </g>
    </svg>
    <span class="web__url">www.fernleafvergeclipping.com.au</span>
  </div>

  <p class="tagline">Have your hedges<br>trimmed <span class="tagline__accent">today!</span></p>
</div>
</body>
</html>
```